New Business Card Design Project

Need a design that will create an impact / strong impression towards our clients for our business. We are in the lighting business and we do lighting retrofits for large commercial to industrial clientele.

Target Market(s)

Lighting Industry

Industry/Entity Type

Business

Font styles to use
Other font styles liked:
• we would like to use the font on our logo, not sure what it is though..

Requirements
Must have
• Our logo.
Nice to have
• We are open to suggestions that have to do with lighting.

```html
<!DOCTYPE html>
<html lang="en">
<head>
<meta charset="utf-8">
<title>Brightline Retrofit Co. — Business Card</title>
<link rel="stylesheet" href="https://fonts.googleapis.com/css2?family=Montserrat:wght@400;600;700&display=swap">
<style>
  :root {
    --backdrop: #2b2b2b;
    --paper: #ffffff;
    --green-light: #5dc15b;
    --green-mid: #0c8a3d;
    --green-dark: #163c11;
    --green-back: #0a8334;
    --ink-light: #ffffff;
  }
  * { margin: 0; padding: 0; box-sizing: border-box; }
  html, body {
    width: 1200px; height: 960px; overflow: hidden;
    background: var(--backdrop);
    font-family: "Montserrat", Arial, sans-serif;
  }
  .canvas { position: relative; width: 1200px; height: 960px; }

  .card { position: absolute; width: 600px; height: 342px; overflow: hidden; }
  .card-front { left: 314px; top: 113px; background: var(--paper); }
  .card-back { left: 311px; top: 472px; background: var(--green-back); }

  .wordmark {
    position: absolute; left: 0; right: 0;
    display: flex; align-items: center; justify-content: center; gap: 14px;
    font-weight: 700; font-size: 34px; letter-spacing: 0.5px;
  }
  .wordmark-mark { width: 20px; height: 20px; }
  .card-front .wordmark { top: 78px; color: var(--green-dark); }
  .card-front .wordmark-mark { background: var(--green-mid); }
  .card-back .wordmark { top: 122px; color: var(--ink-light); }
  .card-back .wordmark-mark { background: var(--ink-light); }

  .stripe-row {
    position: absolute; left: 0; top: 205px; width: 600px; height: 5px;
    display: flex; gap: 2px;
  }
  .stripe { flex: 1; }
  .stripe.light { background: var(--green-light); }
  .stripe.mid { background: var(--green-mid); }
  .stripe.dark { background: var(--green-dark); }

  .contact-band {
    position: absolute; left: 0; top: 213px; width: 600px; height: 129px;
    background: var(--green-dark); color: var(--ink-light);
  }
  .identity { position: absolute; left: 28px; top: 20px; }
  .person-name { font-size: 19px; font-weight: 700; letter-spacing: 0.3px; }
  .person-role { font-size: 16px; font-weight: 400; margin-top: 2px; letter-spacing: 0.3px; }
  .address { font-size: 15px; margin-top: 6px; line-height: 20px; letter-spacing: 0.3px; }

  .contact-list {
    position: absolute; right: 28px; top: 29px;
    list-style: none; text-align: right;
  }
  .contact-list li {
    display: flex; justify-content: flex-end; align-items: center; gap: 8px;
    font-size: 15px; line-height: 19.5px; letter-spacing: 0.3px;
  }
  .contact-list li.small { font-size: 13px; }
  .contact-list svg { width: 12px; height: 12px; fill: var(--ink-light); }

  .website {
    position: absolute; left: 0; right: 0; top: 282px;
    text-align: center; color: var(--ink-light);
    font-size: 14px; letter-spacing: 2px;
  }
</style>
</head>
<body>
<main class="canvas">

  <section class="card card-front" aria-label="Business card front">
    <div class="wordmark"><span class="wordmark-mark"></span>Brightline Retrofit Co.</div>

    <div class="stripe-row">
      <span class="stripe light"></span><span class="stripe mid"></span><span class="stripe dark"></span>
      <span class="stripe light"></span><span class="stripe mid"></span><span class="stripe dark"></span>
    </div>

    <div class="contact-band">
      <div class="identity">
        <p class="person-name">DANA WHITFIELD</p>
        <p class="person-role">CEO/FOUNDER</p>
        <p class="address">1200 Alder Street<br>Juneau, Alaska 99801</p>
      </div>
      <ul class="contact-list">
        <li>555 014 2210
          <svg viewBox="0 0 12 12" aria-label="Office phone"><path d="M1 4c0-2 2-3 5-3s5 1 5 3v1H8.5V3.8c-1.5-.5-3.5-.5-5 0V5H1zM3 6h6l1 5H2z"/></svg>
        </li>
        <li>555 019 4482
          <svg viewBox="0 0 12 12" aria-label="Mobile"><path d="M3 0h6v12H3zM4 1.5v7.5h4V1.5z"/></svg>
        </li>
        <li class="small">555 017 3306
          <svg viewBox="0 0 12 12" aria-label="Fax"><path d="M3 1h6v3H3zM0 5h12v5H9v1H3v-1H0zM4 8v2h4V8z"/></svg>
        </li>
        <li>dana@brightline.co
          <svg viewBox="0 0 12 12" aria-label="Email"><path d="M0 2.5h12v1L6 7 0 3.5zM0 4.8 6 8.3l6-3.5V10H0z"/></svg>
        </li>
      </ul>
    </div>
  </section>

  <section class="card card-back" aria-label="Business card back">
    <div class="wordmark"><span class="wordmark-mark"></span>Brightline Retrofit Co.</div>
    <p class="website">www.brightlineretrofit.com</p>
  </section>

</main>
</body>
</html>
```